Northfield Builders Guild Business card

We are looking for a new business card design with photo included.
Our business is a nonprofit construction contractor membership organization. We offer business education, assist with business setup and licensing, provide safety training, and provide a member directory.
URL: www.builderslinkguild.org
Color code:
CMYK: 0 cyan, 42 magenta, 100 yellow, 0 black for Print.
Hexidecimal: #FF9900
RGB: R 255; G 153; B 0

```html
<!DOCTYPE html>
<html lang="en">
<head>
<meta charset="utf-8">
<title>Northfield Builders Guild – Business Card</title>
<link rel="stylesheet" href="https://fonts.googleapis.com/css2?family=Montserrat:wght@400;500;600;800&display=swap">
<style>
  :root{
    --orange:#ff9900;
    --charcoal:#333132;
    --ink:#2b2b2b;
    --paper:#ffffff;
    --stage:#1c1c1c;
    --rule:#c8c8c8;
  }
  *{box-sizing:border-box;margin:0;padding:0}
  html,body{width:1200px;height:1015px;overflow:hidden;background:var(--stage);font-family:"Montserrat",sans-serif}
  .card{position:absolute;left:250px;width:700px;height:400px;overflow:hidden}
  .card--front{top:80px;background:var(--charcoal)}
  .card--back{top:535px;background:var(--paper)}

  .brand{font-weight:800;text-transform:uppercase;line-height:1.02;letter-spacing:-0.5px}
  .card--front .brand{position:absolute;left:0;right:0;top:70px;text-align:center;color:var(--paper);font-size:46px}

  .services{position:absolute;left:0;right:0;top:225px;height:86px;background:var(--orange);
    display:flex;flex-direction:column;justify-content:center;align-items:center;gap:6px;
    color:var(--paper);font-size:17px;font-weight:500}
  .services .dot{display:inline-block;width:7px;height:7px;border-radius:50%;background:var(--paper);margin:0 10px;vertical-align:middle}

  .card--back .brand{position:absolute;left:40px;top:140px;width:270px;color:var(--ink);font-size:34px}
  .divider{position:absolute;left:320px;top:50px;width:1px;height:235px;background:var(--rule)}
  .contact{position:absolute;left:345px;top:48px;color:var(--ink)}
  .contact .name{font-weight:800;font-size:24px;text-transform:uppercase;letter-spacing:-0.3px}
  .contact .role{color:var(--orange);font-weight:500;font-size:15px;text-transform:uppercase;margin-bottom:12px}
  .contact ul{list-style:none}
  .contact li{display:flex;align-items:center;gap:8px;font-size:15px;height:23px}
  .contact .icon{width:18px;height:18px;flex:none}
  .contact .accent{color:var(--orange)}
  .contact address{font-style:normal;font-size:16px;font-weight:500;margin-top:16px;line-height:1.3}

  .strip-orange{position:absolute;left:0;bottom:0;width:465px;height:22px;background:var(--orange)}
  .block-dark{position:absolute;left:468px;bottom:0;width:232px;height:58px;background:var(--charcoal)}
</style>
</head>
<body>

<section class="card card--front">
  <h1 class="brand">Northfield<br>Builders Guild</h1>
  <div class="services">
    <p>Business education<span class="dot"></span>Assist with business setup and licensing</p>
    <p>Provide safety training<span class="dot"></span>Provide a member directory</p>
  </div>
</section>

<section class="card card--back">
  <h2 class="brand">Northfield<br>Builders Guild</h2>
  <div class="divider"></div>
  <div class="contact">
    <p class="name">Daniel Harper</p>
    <p class="role">Managing Director</p>
    <ul>
      <li><svg class="icon" viewBox="0 0 18 18"><circle cx="9" cy="9" r="9" fill="var(--orange)"/><path d="M6 5l2 2-1 1.2a5 5 0 0 0 2.8 2.8L11 10l2 2-1.2 1.2C8.5 13 5 9.5 4.8 6.2z" fill="#fff"/></svg>(555) 201-3384 (Office)</li>
      <li><svg class="icon" viewBox="0 0 18 18"><circle cx="9" cy="9" r="9" fill="var(--orange)"/><rect x="6" y="4" width="6" height="10" rx="1" fill="none" stroke="#fff" stroke-width="1.4"/></svg>800-555-0147</li>
      <li><svg class="icon" viewBox="0 0 18 18"><circle cx="9" cy="9" r="9" fill="var(--orange)"/><rect x="5" y="8" width="8" height="5" fill="#fff"/><rect x="6.5" y="5" width="5" height="3" fill="#fff"/></svg>555.310.0926</li>
      <li><svg class="icon" viewBox="0 0 18 18"><circle cx="9" cy="9" r="9" fill="var(--orange)"/><rect x="4.5" y="6" width="9" height="6.5" fill="none" stroke="#fff" stroke-width="1.3"/><path d="M4.5 6l4.5 4 4.5-4" fill="none" stroke="#fff" stroke-width="1.3"/></svg>support@nbguild.org</li>
      <li><svg class="icon" viewBox="0 0 18 18"><circle cx="9" cy="9" r="9" fill="var(--orange)"/><circle cx="9" cy="9" r="4.5" fill="none" stroke="#fff" stroke-width="1.2"/><path d="M4.5 9h9M9 4.5v9" stroke="#fff" stroke-width="1.2"/></svg>www.<span class="accent">builderslinkguild</span>.org</li>
    </ul>
    <address>2400 Ridgeline Ave<br>Suite #210, Fairview, OR 97000</address>
  </div>
  <div class="strip-orange"></div>
  <div class="block-dark"></div>
</section>

</body>
</html>
```